Consulting company business cards

We have a base design, but would be willing to update. We have a new logo/"tag" that needs to be added. Current business card design is attached for reference into our "style."

Industry/Entity Type

Business

Contact Information for Business Card

Should contain name and title, office number, mobile number if appropriate, e-mail, website, physical address, and company logo.

Font styles to use
Other font styles liked:
• See current card design on KorvandBCard

Colors
0455a3
85acd3
aaaaaa

Requirements
Must have
• Our colors are navy blue, gray, and a lighter blue
Nice to have
• Design that I can easily drop in new names/titles as we hire employees.

```html
<!DOCTYPE html>
<html lang="en">
<head>
<meta charset="utf-8">
<title>Halden business cards</title>
<link rel="stylesheet" href="https://fonts.googleapis.com/css2?family=PT+Sans:wght@400;700&display=swap">
<style>
  :root {
    --page-bg: #3a332e;
    --card-dark: #1b1b1d;
    --card-blue-top: #0d4766;
    --card-blue-bottom: #062f4a;
    --navy: #0455a3;
    --navy-deep: #1d4f7c;
    --light-blue: #85acd3;
    --gray: #aaaaaa;
    --white: #f2f2f2;
  }
  * { margin: 0; padding: 0; box-sizing: border-box; }
  html, body { width: 1200px; height: 844px; overflow: hidden; }
  body {
    background: var(--page-bg);
    font-family: "PT Sans", Arial, sans-serif;
    position: relative;
  }
  .card {
    position: absolute;
    top: 273px;
    width: 520px;
    height: 298px;
    border-radius: 3px;
    box-shadow: 0 12px 30px rgba(0,0,0,0.45);
  }
  .card-front { left: 50px; background: var(--card-dark); }
  .card-back {
    left: 630px;
    background: linear-gradient(135deg, var(--card-blue-top), var(--card-blue-bottom));
  }

  .brand { position: absolute; display: flex; flex-direction: column; }
  .brand-row { display: flex; align-items: center; gap: 10px; }
  .brand-name {
    font-weight: 700;
    letter-spacing: 3px;
    line-height: 1;
  }
  .brand-mark { border-radius: 50%; }
  .brand-tagline {
    font-weight: 400;
    letter-spacing: 2.6px;
    text-transform: uppercase;
    margin-top: 4px;
  }

  .card-front .brand { left: 148px; top: 42px; }
  .card-front .brand-name { font-size: 58px; color: var(--navy-deep); }
  .card-front .brand-mark { width: 44px; height: 44px; background: var(--light-blue); }
  .card-front .brand-tagline { font-size: 14px; color: var(--white); }

  .card-back .brand { left: 118px; top: 88px; }
  .card-back .brand-name { font-size: 68px; color: var(--light-blue); }
  .card-back .brand-mark { width: 52px; height: 52px; background: var(--light-blue); }
  .card-back .brand-tagline { font-size: 15px; color: var(--light-blue); }

  .person {
    position: absolute;
    right: 268px;
    top: 168px;
    text-align: right;
    color: var(--white);
    font-size: 15px;
    line-height: 1.35;
  }
  .person-name { color: var(--navy-deep); font-size: 17px; }
  .person-title { margin-bottom: 14px; }

  .divider {
    position: absolute;
    left: 264px;
    top: 166px;
    width: 1px;
    height: 104px;
    background: #3c3c40;
  }

  .contact-list {
    position: absolute;
    left: 278px;
    top: 166px;
    list-style: none;
    color: var(--white);
    font-size: 14.5px;
    line-height: 1.45;
  }
  .contact-list li { display: flex; align-items: center; gap: 7px; }
  .contact-list svg { width: 10px; height: 10px; flex: none; fill: var(--navy-deep); }
</style>
</head>
<body>
  <section class="card card-front" aria-label="Business card front">
    <div class="brand">
      <div class="brand-row">
        <span class="brand-name">HALDEN</span>
        <span class="brand-mark"></span>
      </div>
      <span class="brand-tagline">A Cloud Consulting Company</span>
    </div>

    <div class="person">
      <p class="person-name">Hanna Korvand</p>
      <p class="person-title">Managing Director</p>
      <p class="person-address">1185 N 48 th fernwood<br>ohio 43017</p>
    </div>

    <div class="divider"></div>

    <ul class="contact-list">
      <li><svg viewBox="0 0 10 10"><circle cx="5" cy="5" r="4.5"/></svg>555.204.3910</li>
      <li><svg viewBox="0 0 10 10"><circle cx="5" cy="5" r="4.5"/></svg>555.204.3971</li>
      <li><svg viewBox="0 0 10 10"><circle cx="5" cy="5" r="4.5"/></svg>hkorvand@haldentech.com</li>
      <li><svg viewBox="0 0 10 10"><circle cx="5" cy="5" r="4.5"/></svg>www.haldentech.com</li>
    </ul>
  </section>

  <section class="card card-back" aria-label="Business card back">
    <div class="brand">
      <div class="brand-row">
        <span class="brand-name">HALDEN</span>
        <span class="brand-mark"></span>
      </div>
      <span class="brand-tagline">A Cloud Consulting Company</span>
    </div>
  </section>
</body>
</html>
```